We are a local Communty Pharmacy wishing to promote and market a specialised Pharmaceutical Service

We would like a design that is professional and enticing ( according to the brief In attached files)
We wish to Market Compounding Pharmacy as a specialist side of our business.
We have the expertise a purpose built preparation laboratory.
The main purpose is an Internet presence that entices prospective patients to contact or visit our physical store.

Target Market(s)

Patients Medicos and Veterinary clients

Industry/Entity Type

Pharmacy

Coding

Coded - Design and coding required

Number of Pages Required

1 page

Requirements
Must have
• Clear friendly image
Nice to have
• soft enticing feel
Should not have
• No crass loud unprofessional elements

```html
<!DOCTYPE html>
<html lang="en">
<head>
<meta charset="utf-8">
<title>Kestrel Vale Pharmacy – Compounding</title>
<link href="https://fonts.googleapis.com/css2?family=Open+Sans:wght@400;600;700&family=Oswald:wght@500;700&display=swap" rel="stylesheet">
<style>
:root{
  --green:#8cc63f;
  --green-dark:#6fa82a;
  --active:#f2c21b;
  --blue:#1f6fb5;
  --navy:#15233f;
  --navy-deep:#0e182d;
  --text:#4a4f57;
  --white:#ffffff;
}
*{box-sizing:border-box;margin:0;padding:0}
html,body{width:822px;height:1200px;overflow:hidden;background:var(--white)}
body{font-family:"Open Sans",Arial,sans-serif;color:var(--text);position:relative}
.wrap{width:614px;margin:0 auto;position:relative}

.site-header{height:88px}
.site-header .wrap{display:flex;align-items:center;height:88px;justify-content:space-between}
.brand{display:flex;align-items:center;gap:10px;font-weight:700;color:var(--blue);font-size:17px;width:200px}
.brand-mark{width:22px;height:22px;border-radius:50%;background:var(--green)}
.address{font-size:9.5px;line-height:14px;color:var(--text);width:150px}
.contact-list{font-size:9.5px;line-height:16px;width:210px}
.contact-list li{list-style:none;display:flex;align-items:center;gap:6px}
.contact-list svg{width:10px;height:10px;fill:var(--blue)}

.main-nav{height:24px;background:var(--green)}
.main-nav .wrap{display:flex;height:24px;align-items:stretch}
.main-nav a{color:var(--white);font-size:9.5px;font-weight:700;text-decoration:none;padding:0 17px;display:flex;align-items:center;letter-spacing:.5px}
.main-nav a.active{background:var(--active);color:var(--navy)}
.main-nav .search{margin-left:auto;width:24px;justify-content:center;padding:0;background:var(--green-dark)}

.hero{position:relative;height:276px;background:linear-gradient(100deg,#e8eef2 0%,#d5dde4 45%,#b9c7d3 70%,#9fb2c4 100%)}
.hero-text{position:absolute;left:300px;right:60px;top:130px;text-align:center;color:var(--white)}
.hero-text h1{font-family:"Oswald",sans-serif;font-weight:700;font-size:34px;letter-spacing:2px;line-height:40px;background:rgba(31,111,181,.55);padding:2px 10px}
.hero-text .is{font-family:"Oswald",sans-serif;font-size:26px;font-weight:700;margin:4px 0}
.hero-text p{font-family:"Oswald",sans-serif;font-size:15px;font-weight:500;letter-spacing:1px}
.dots{position:absolute;bottom:12px;left:0;right:0;display:flex;justify-content:center;gap:6px}
.dots span{width:7px;height:7px;border-radius:50%;background:rgba(255,255,255,.6)}
.dots span.on{background:var(--white)}

.about{padding:40px 0 30px;height:438px}
.about h2{color:var(--blue);font-size:17px;font-weight:700;margin-bottom:16px}
.about p{font-size:11.5px;line-height:21px;margin-bottom:14px;text-align:justify}

.services{display:flex;height:198px}
.tile{flex:1;position:relative}
.tile:nth-child(1){background:linear-gradient(135deg,#d9c7c0,#8f7d78)}
.tile:nth-child(2){background:linear-gradient(135deg,#c7b8b1,#6b5d5a)}
.tile:nth-child(3){background:linear-gradient(135deg,#d6d9dc,#8a9096)}
.tile span{position:absolute;left:16px;bottom:14px;color:var(--white);font-family:"Oswald",sans-serif;font-size:16px;font-weight:700;letter-spacing:1.5px}

.site-footer{background:var(--navy);height:180px;color:var(--white)}
.site-footer .wrap{display:flex;justify-content:space-between;padding-top:22px;height:158px}
.site-footer h3{font-size:10.5px;font-weight:700;margin-bottom:12px;letter-spacing:.5px}
.site-footer p{font-size:9.5px;line-height:16px}
.map{width:210px;height:108px;background:linear-gradient(135deg,#e4e7ea,#c9ced4)}
.footer-contacts{width:170px}
.footer-base{background:var(--navy-deep);height:22px}
</style>
</head>
<body>
<header class="site-header">
  <div class="wrap">
    <div class="brand"><span class="brand-mark"></span>Kestrel Vale Pharmacy</div>
    <p class="address">Unit 4 Larkspur Road<br>Kestrel Vale Plaza<br>6100 Western Australia</p>
    <ul class="contact-list">
      <li><svg viewBox="0 0 10 10"><path d="M2 0l2 2-1 1.5c.8 1.6 2 2.8 3.5 3.5L8 6l2 2-1.5 2C4 9.5.5 6 0 1.5z"/></svg>08 5550 1420</li>
      <li><svg viewBox="0 0 10 10"><rect x="0" y="2" width="10" height="6"/></svg>08 5550 1420</li>
      <li><svg viewBox="0 0 10 10"><path d="M0 2h10v6H0z M0 2l5 3 5-3" /></svg>compounding@kestrelvale.example</li>
    </ul>
  </div>
</header>

<nav class="main-nav">
  <div class="wrap">
    <a class="active">HOME</a><a>ABOUT US</a><a>LOCATIONS</a><a>PRICING</a><a>CONTACT</a>
    <a class="search"><svg width="11" height="11" viewBox="0 0 11 11"><circle cx="4.5" cy="4.5" r="3.3" fill="none" stroke="#fff" stroke-width="1.5"/><path d="M7 7l3.3 3.3" stroke="#fff" stroke-width="1.6"/></svg></a>
  </div>
</nav>

<section class="hero" role="img" aria-label="Pharmacist in a lab coat examining a compounding sample in the laboratory">
  <div class="hero-text">
    <h1>COMPOUNDING PHARMACY</h1>
    <div class="is">IS</div>
    <p>CUSTOMIZED MEDICATIONS FOR PATIENTS</p>
  </div>
  <div class="dots"><span></span><span class="on"></span><span></span><span></span></div>
</section>

<section class="about">
  <div class="wrap">
    <h2>What is Compounding Pharmacy?</h2>
    <p>Compounding is the craft of preparing medicines to suit one person rather than a population. Our pharmacists combine ingredients in exact strengths and forms when a standard product is unsuitable, unavailable or poorly tolerated, working closely with prescribers at every step.</p>
    <p>We prepare creams, capsules, lozenges, oral liquids and flavoured doses for children and animals in a purpose built laboratory. Each preparation is checked, labelled and explained so that patients, doctors and veterinary clients can trust what they receive.</p>
    <p>Visit our store or call the compounding team to discuss a prescription, ask about ingredients or arrange collection. We are happy to talk through options and find a preparation that fits your needs.</p>
    <p>Our compounding service works alongside your usual pharmacy care, with the same friendly staff and convenient opening hours seven days a week.</p>
  </div>
</section>

<section class="services">
  <div class="tile" role="img" aria-label="Hands applying a compounded cream"><span>ARTICLE</span></div>
  <div class="tile" role="img" aria-label="Close view of scar treatment being applied to skin"><span>SCAR THERAPY</span></div>
  <div class="tile" role="img" aria-label="Thyroid area of the neck"><span>THYROID EXTRACT</span></div>
</section>

<footer class="site-footer">
  <div class="wrap">
    <div class="footer-hours">
      <h3>HOURS</h3>
      <p>7 DAYS A WEEK<br>8.00 AM TO 8.30 PM</p>
    </div>
    <div class="map" role="img" aria-label="Street map showing the pharmacy location"></div>
    <div class="footer-contacts">
      <h3>CONTACTS</h3>
      <p>PHONE : 08 5550 1420</p>
      <p>FAX : 08 5550 1420</p>
      <p style="margin-top:10px">E-mail : compounding@kestrelvale.example</p>
    </div>
  </div>
  <div class="footer-base"></div>
</footer>
</body>
</html>
```